Design a New Business Card for Our Company

We are looking for fresh, unique, and a modern business card that reflects our roots as digital marketing agency focused on SEM.

Industry/Entity Type

Marketing

Contact Information for Business Card

looking for very unique out of the box designs. clean and modern that compliments our logo

Requirements
Must have
• colors should match our logo
• Front should have name, address, email, and phone/fax of the person, phone/fax are the same number
• back should have our url

```html
<!DOCTYPE html>
<html lang="en">
<head>
<meta charset="utf-8">
<title>Brightcell Media business card</title>
<link href="https://fonts.googleapis.com/css2?family=Arimo:wght@400;700&display=swap" rel="stylesheet">
<style>
  :root {
    --backdrop: #4a423d;
    --card: #1b1b1c;
    --card-edge: #111112;
    --ink: #e9e9ea;
    --ink-soft: #bdbdbf;
    --accent: #4a90d9;
    --rule: #7a7a7c;
  }
  * { margin: 0; padding: 0; box-sizing: border-box; }
  html, body {
    width: 1200px; height: 787px; overflow: hidden;
    background: var(--backdrop);
    font-family: "Arimo", Arial, sans-serif;
  }
  .stage { position: relative; width: 1200px; height: 787px; }
  .card {
    position: absolute;
    width: 560px; height: 320px;
    background: var(--card);
    border: 1px solid var(--card-edge);
    border-radius: 4px;
    box-shadow: 0 10px 30px rgba(0,0,0,.35);
  }
  .card--back { left: 40px; top: 50px; }
  .card--front { left: 600px; top: 400px; }

  .brand { display: flex; align-items: center; gap: 14px; }
  .brand__dot {
    width: 38px; height: 38px; border-radius: 50%;
    background: var(--accent); flex: none;
  }
  .brand__name {
    font-weight: 700; font-size: 42px; letter-spacing: -1px;
    color: var(--ink);
  }

  .card--back .brand { position: absolute; left: 70px; top: 90px; }
  .card--back .brand__dot { background: #9a9a9c; }
  .card--back .brand__name { color: #a8a8aa; }
  .website {
    position: absolute; left: 70px; top: 210px;
    font-size: 15px; letter-spacing: 5px; color: var(--ink);
  }

  .card--front .brand { position: absolute; left: 150px; top: 70px; }
  .person {
    position: absolute; left: 100px; top: 200px; text-align: right; width: 150px;
  }
  .person__name { font-weight: 700; font-size: 20px; color: var(--ink-soft); }
  .person__role { font-size: 17px; color: var(--accent); margin-top: 4px; }
  .divider {
    position: absolute; left: 270px; top: 188px;
    width: 1px; height: 100px; background: var(--rule);
  }
  .contact {
    position: absolute; left: 290px; top: 190px;
    font-size: 17px; line-height: 22px; color: var(--ink);
    list-style: none;
  }
  .contact li { display: flex; align-items: center; gap: 10px; }
  .contact__icon { width: 16px; height: 16px; flex: none; fill: var(--ink); }
  .contact__pad { width: 16px; flex: none; }
</style>
</head>
<body>
<main class="stage">
  <section class="card card--back" aria-label="Card back">
    <div class="brand">
      <span class="brand__dot"></span>
      <span class="brand__name">Brightcell Media</span>
    </div>
    <p class="website">www.brightcellmedia.com</p>
  </section>

  <section class="card card--front" aria-label="Card front">
    <div class="brand">
      <span class="brand__dot"></span>
      <span class="brand__name">Brightcell Media</span>
    </div>
    <div class="person">
      <p class="person__name">Mark Ellison</p>
      <p class="person__role">President</p>
    </div>
    <div class="divider"></div>
    <ul class="contact">
      <li><span class="contact__pad"></span>2710 Harbor View Lane</li>
      <li><span class="contact__pad"></span>Maple Ridge, NY 11020</li>
      <li>
        <svg class="contact__icon" viewBox="0 0 16 16" aria-label="Phone"><path d="M3 1h3l1 4-2 1a9 9 0 0 0 5 5l1-2 4 1v3a2 2 0 0 1-2 2A13 13 0 0 1 1 3a2 2 0 0 1 2-2z"/></svg>
        412 7390 5518
      </li>
      <li>
        <svg class="contact__icon" viewBox="0 0 16 16" aria-label="Fax"><rect x="4" y="1" width="8" height="4"/><rect x="1" y="6" width="14" height="6" rx="1"/><rect x="4" y="10" width="8" height="5"/></svg>
        648 2915 7043
      </li>
      <li>
        <svg class="contact__icon" viewBox="0 0 16 16" aria-label="Email"><path d="M1 3h14v10H1z M2 4l6 5 6-5" fill="none" stroke="#e9e9ea" stroke-width="1.4"/></svg>
        mark@brightcellmedia.com
      </li>
    </ul>
  </section>
</main>
</body>
</html>
```